Building Referrer Relationships Booklet

4 page A4 booklet to give to potential professional referrers to establish a collaborative relationship.Needs to be bright, vibrant, colourful, friendly, inviting, in keeping with The Linden Practice colours.
Want to provide potential referrer partners a great reason to choose to collaborate with us. They need to know who we are, what makes us different/appealing, and who we are looking for to connect with.
The final product should communicate high performance and connectedness.
Updates

Target Market(s)

professional medical allied health and fitness practitioners

Industry/Entity Type

Health

Requirements
Must have
• energetic, vibrant, engaging, inviting, images

```html
<!DOCTYPE html>
<html lang="en">
<head>
<meta charset="utf-8">
<title>The Linden Practice – Referrer Booklet Cover</title>
<link rel="stylesheet" href="https://fonts.googleapis.com/css2?family=Arimo:wght@700&display=swap">
<style>
  :root {
    --canvas-bg: #eef0f1;
    --photo-light: #f4f6f7;
    --photo-mid: #e3e7ea;
    --photo-coat: #dfe3e8;
    --photo-accent: #b9cbe0;
    --panel-top: #4f7e9f;
    --panel-bottom: #8fb1bd;
    --rule: #ffffff;
    --text-light: #ffffff;
    --tagline: #f25c05;
  }
  * { margin: 0; padding: 0; box-sizing: border-box; }
  html, body {
    width: 1200px;
    height: 902px;
    overflow: hidden;
    background: var(--canvas-bg);
  }
  body { font-family: "Arimo", "Helvetica Neue", Arial, sans-serif; font-weight: 700; }

  .cover {
    position: relative;
    width: 1200px;
    height: 902px;
    overflow: hidden;
  }

  .hero-photo {
    position: absolute;
    inset: 0;
    background:
      radial-gradient(ellipse 420px 620px at 980px 420px, var(--photo-coat) 0%, rgba(223,227,232,0) 100%),
      linear-gradient(90deg, var(--photo-light) 0%, var(--photo-mid) 60%, var(--photo-accent) 100%);
  }

  .brand-panel {
    position: absolute;
    left: 47px;
    top: 66px;
    width: 468px;
    height: 770px;
    background: linear-gradient(160deg, var(--panel-top) 0%, #6f97b2 50%, var(--panel-bottom) 100%);
    box-shadow: 0 6px 14px rgba(0,0,0,0.25);
  }

  .rule {
    position: absolute;
    background: var(--rule);
    box-shadow: 0 3px 5px rgba(0,0,0,0.25);
  }

  .logo-slot {
    position: absolute;
    left: 96px;
    top: 310px;
    font-size: 24px;
    color: var(--text-light);
    letter-spacing: 0.2px;
    text-shadow: 0 2px 4px rgba(0,0,0,0.3);
  }

  .practice-name {
    position: absolute;
    left: 78px;
    top: 560px;
    font-size: 62px;
    line-height: 68px;
    color: var(--text-light);
    text-transform: uppercase;
    letter-spacing: 0.5px;
  }

  .tagline {
    position: absolute;
    left: 578px;
    top: 628px;
    font-size: 54px;
    line-height: 63px;
    color: var(--tagline);
    text-shadow: 0 2px 4px rgba(0,0,0,0.25);
  }
</style>
</head>
<body>
  <main class="cover">
    <div class="hero-photo" role="img" aria-label="Bright clinical photo of a practitioner in a white coat holding a stethoscope against their chest"></div>

    <section class="brand-panel"></section>

    <div class="rule" style="left:95px; top:292px; width:372px; height:5px;"></div>
    <p class="logo-slot">LOGO SHOULD GO HERE</p>
    <div class="rule" style="left:95px; top:357px; width:372px; height:10px;"></div>

    <div class="rule" style="left:76px; top:536px; width:434px; height:4px;"></div>
    <h1 class="practice-name">The Linden<br>Practice</h1>
    <div class="rule" style="left:76px; top:717px; width:434px; height:11px;"></div>

    <div class="rule" style="left:577px; top:602px; width:534px; height:5px;"></div>
    <p class="tagline">Because<br>together we<br>achieve more.</p>
    <div class="rule" style="left:577px; top:836px; width:534px; height:10px;"></div>
  </main>
</body>
</html>
```